Fitness Equipment & Service

I want to make the card eye catching and fun. We are called Corvane Motion Limited and we are based in Wales. We sell, install and service all types of fitness equipment from Skipping ropes, right through the Dumbbells, Kettle bells and Barbells through to state of the art Treadmills, Running Machines and Strength Equipment. We also design and install changing room furniture and lockers.

TYPOGRAPHY
We would like to use Futrura. Futura has an appearance of efficiency and forwardness. The typeface is derived
from simple geometric forms (near-perfect circles, triangles and squares) and is based on strokes of
near-even weight, which are low in contrast. This is most visible in the almost perfectly round stroke of
the o, which is nonetheless slightly ovoid.
The lowercase has tall ascenders, which rise above the cap line. The uppercase
characters present proportions similar to those of classical Roman capitals.

TYPOGRAPHIC CONSIDERATIONS
No Strike though
No Horizontal Scaling
No Drop Shadows
No Effects
Never use less than 120% Leading

OUR CORPORATE COLOURS
BRAND GUIDELINES
We were thinking that our primary colour palette consists of the Acid Green (Pantone 382) and Process Black.

We work closely with tquarly Ltd and would like to include their name on the card somewhere. I have attached images of the other brands that we work with as an idea or the small icons I have included that illustrate what we do?. I have very kindly been given permission to use any of the images off the files that I have included below, so I hope these help. I will include these below. I would be open to suggestions if it made the card more striking Can you do it?
Updates

Hi All, Just wanted to add a few thoughts but you are the guys with the creative visions (thats why are here) We are based in Wales, UK and we would be open to lots of different ideas on a theme but must be eye catching, Bold and FUN. If you can or think that the Welsh or any dragon could be put in there then go for it (its not a must have) We have also added some ideas for colour but again its over to you!! GO FOR IT ! Thanks and look forward to your visions! Owen

Hi All, Just thought I would sen through the contact details that need to be on the card. (if you want to play around with icons instead of the wording twitter, Facebook, go for it): Corvane Motion Limited Owen Pritchard Managing Director Mob: +44 (0)7582 913 406 e-mail: sales@corvanemotion.co.uk Web: Corvanemotion.co.uk twitter: @motionLetterbin Facebook: Corvane Motion Limited

```html
<!DOCTYPE html>
<html lang="en">
<head>
<meta charset="utf-8">
<title>Corvane Motion Limited – Business Card</title>
<link href="https://fonts.googleapis.com/css2?family=Jost:wght@400;500&display=swap" rel="stylesheet">
<style>
  :root {
    --page: #e6e6e6;
    --acid-light: #d4e43a;
    --acid: #c4d600;
    --acid-dark: #a3b300;
    --black: #111111;
    --black-soft: #2a2a2a;
    --rim: #ffffff;
    --card-white: #ffffff;
    --ink: #111111;
  }
  * { margin: 0; padding: 0; box-sizing: border-box; }
  html, body { width: 1105px; height: 1200px; overflow: hidden; }
  body {
    background: var(--page);
    font-family: "Jost", "Futura", sans-serif;
    position: relative;
  }
  .card {
    position: absolute;
    left: 182px;
    width: 746px;
    height: 427px;
    overflow: hidden;
  }
  .card--front {
    top: 119px;
    background: radial-gradient(ellipse at 55% 25%, var(--acid-light) 0%, var(--acid) 45%, var(--acid-dark) 100%);
    color: var(--ink);
  }
  .card--back {
    top: 637px;
    background: var(--card-white);
  }
  .globe {
    position: absolute;
    left: 342px;
    top: -8px;
    width: 456px;
    height: 456px;
    border-radius: 50%;
    border: 4px solid var(--rim);
    background: radial-gradient(circle at 55% 35%, var(--black-soft) 0%, var(--black) 70%);
  }
  .globe__name {
    position: absolute;
    left: 372px;
    top: 150px;
    width: 340px;
    text-align: center;
    font-size: 36px;
    font-weight: 500;
    line-height: 1.25;
    color: var(--acid);
  }
  .holder__name {
    position: absolute;
    left: 30px;
    top: 30px;
    font-size: 31px;
    font-weight: 500;
    line-height: 1.2;
  }
  .holder__title {
    position: absolute;
    left: 30px;
    top: 70px;
    font-size: 23px;
    font-weight: 400;
    line-height: 1.2;
  }
  .address {
    position: absolute;
    left: 30px;
    top: 192px;
    font-size: 20px;
    line-height: 1.25;
    font-style: normal;
  }
  .contacts {
    position: absolute;
    left: 34px;
    top: 262px;
    list-style: none;
    font-size: 19.5px;
    line-height: 1.2;
  }
  .contacts li {
    display: flex;
    align-items: center;
    height: 28.5px;
  }
  .contacts svg {
    width: 17px;
    height: 17px;
    margin-right: 10px;
    flex: none;
  }
  .brand {
    position: absolute;
    left: 0;
    right: 0;
    top: 170px;
    display: flex;
    align-items: center;
    justify-content: center;
    gap: 16px;
  }
  .brand__dot {
    width: 34px;
    height: 34px;
    border-radius: 50%;
    background: var(--acid);
  }
  .brand__name {
    font-size: 32px;
    font-weight: 500;
    color: var(--black);
    line-height: 1.2;
  }
  .partner {
    position: absolute;
    left: 0;
    right: 0;
    top: 232px;
    text-align: center;
    font-size: 17px;
    font-weight: 400;
    line-height: 1.3;
    color: var(--black);
  }
</style>
</head>
<body>

<section class="card card--front">
  <div class="globe" role="img" aria-label="Stylised world map on a dark globe"></div>
  <p class="globe__name">Corvane Motion<br>Limited</p>

  <h1 class="holder__name">Owen Pritchard</h1>
  <p class="holder__title">Managing Director</p>

  <address class="address">19 Heronfield Row<br>Brecon, Powys LD3 7QX</address>

  <ul class="contacts">
    <li>
      <svg viewBox="0 0 16 16" aria-hidden="true"><rect x="4" y="1" width="8" height="14" rx="1.5" fill="none" stroke="#111" stroke-width="1.6"/><circle cx="8" cy="12.5" r="0.9" fill="#111"/></svg>
      +44 (0)7582 913 406
    </li>
    <li>
      <svg viewBox="0 0 16 16" aria-hidden="true"><rect x="1" y="3" width="14" height="10" fill="#111"/><path d="M1 3 L8 9 L15 3" fill="none" stroke="#c4d600" stroke-width="1.2"/></svg>
      sales@corvanemotion.co.uk
    </li>
    <li>
      <svg viewBox="0 0 16 16" aria-hidden="true"><circle cx="8" cy="8" r="6.8" fill="none" stroke="#111" stroke-width="1.5"/><ellipse cx="8" cy="8" rx="3" ry="6.8" fill="none" stroke="#111" stroke-width="1.2"/><line x1="1.2" y1="8" x2="14.8" y2="8" stroke="#111" stroke-width="1.2"/></svg>
      www.Corvanemotion.co.uk
    </li>
    <li>
      <svg viewBox="0 0 16 16" aria-hidden="true"><rect x="1" y="1" width="14" height="14" rx="2" fill="#111"/></svg>
      @motionLetterbin
    </li>
    <li>
      <svg viewBox="0 0 16 16" aria-hidden="true"><rect x="1" y="1" width="14" height="14" rx="2" fill="#111"/></svg>
      Corvane Motion Limited
    </li>
  </ul>
</section>

<section class="card card--back">
  <div class="brand">
    <span class="brand__dot"></span>
    <span class="brand__name">Corvane Motion Limited</span>
  </div>
  <p class="partner">In partnership with tquarly Ltd</p>
</section>

</body>
</html>
```